Yoga Workshop - Yoga Practice information flyer

I am a yoga teacher who will be presenting a workshop on yoga for sleep and need a brochure for my clients which outlines a practice that I give them so they can do the practice at home. Ideally I would like a brochure that is a single A3 size of paper in size that folds in half to an A4 booklet with the entire practice on the centre section to make it easy for people to do the practice at home with just one open page in front of them:
* Front page detailing "Yoga for Sleep Workshop" and "Restorative Yoga Practice"
* Centre contains the information on the practice contained in the attached word document. The practice consists of 5 postures, so there needs to be five separate sections which have the pictures of the postures (attached in uploaded files) and the wording contained in the attached word document. All pictures uploaded need to be included in the flyer as each posture has different pictures demonstrating the posture using yoga props or using things people have at home
* Back page containing a picture of myself (picture uploaded in files) with some information about me (contained in the attached word document) and my website www.calmdrift.com.au

I also need this flyer to be able to printed on 2 double sided A4 sheets of paper so will require 2 x pdf file versions. Importantly, for the centre section of the flyer, the design needs to ensure if it is printed on A4 paper, the wording and pictures for each of the postures are not separated over two pages

Target Market(s)

Existing clients

Requirements
Must have
• Detailed in project description
Nice to have
• The word document also contains some quotes. These do not need to be included in the flyer. If there is room and there is room for one or two of those please include where it would look good
Should not have
• Stock pictures of people in yoga postures which a normal everyday person could not get into

```html
<!DOCTYPE html>
<html lang="en">
<head>
<meta charset="utf-8">
<title>Yoga for Sleep Workshop – Brochure</title>
<link href="https://fonts.googleapis.com/css2?family=Rubik:wght@400;500;700&family=Bebas+Neue&family=Alegreya:wght@700&family=Josefin+Sans:wght@400&display=swap" rel="stylesheet">
<style>
:root{
  --navy:#3b4b65;
  --navy-deep:#2f3f5a;
  --orange:#c98461;
  --peach:#fbe2d7;
  --white:#ffffff;
  --ink:#3a3a3a;
  --backdrop:#ecebe8;
}
*{margin:0;padding:0;box-sizing:border-box}
html,body{width:1200px;height:1200px;overflow:hidden;background:var(--backdrop);font-family:'Rubik',sans-serif}
.spread{position:absolute;left:224px;width:753px;height:533px;box-shadow:0 3px 10px rgba(0,0,0,.18)}
.spread--outer{top:52px}
.spread--inner{top:624px;background:var(--white)}
.page{position:absolute;top:0;width:376.5px;height:100%;overflow:hidden}
.page--left{left:0}
.page--right{left:376.5px}

/* back cover */
.back-cover{background:var(--navy)}
.about-title{position:absolute;left:56px;top:29px;color:var(--white);font-weight:700;font-size:14px;letter-spacing:-.2px}
.about-body{position:absolute;left:56px;top:52px;width:265px;color:var(--white);font-size:5.4px;line-height:7.6px;text-align:justify}
.quote{position:absolute;left:56px;color:var(--white);font-size:5.4px;line-height:7.6px}
.quote-mark{position:absolute;left:0;top:-4px;width:20px;height:16px}
.quote-text{margin-left:35px}
.teacher-photo{position:absolute;left:0;top:310px;width:260px;height:223px}
.website{position:absolute;left:217px;top:401px;color:var(--white);font-size:10.5px;letter-spacing:.2px}

/* front cover */
.front-cover{background:var(--navy)}
.front-art{position:absolute;inset:0}
.brand{position:absolute;left:111px;right:0;top:14px;text-align:center}
.brand-dot{display:block;margin:0 auto 6px;width:36px;height:36px;border-radius:50%;border:2px solid var(--orange)}
.brand-name{font-family:'Alegreya',serif;font-weight:700;font-size:21px;color:var(--navy-deep);line-height:1}
.brand-tagline{font-family:'Josefin Sans',sans-serif;font-size:6.4px;letter-spacing:1.1px;color:var(--navy-deep);margin-top:8px}
.cover-title{position:absolute;right:17px;top:455px;text-align:right;font-family:'Bebas Neue',sans-serif;color:var(--orange);font-size:23px;line-height:24px;letter-spacing:.2px}

/* inside */
.inner-left{background:var(--white)}
.inner-right{background:linear-gradient(90deg,#eeeeee 0,#fafafa 10px,#fff 30px)}
.sequence-title{position:absolute;left:24px;top:22px;font-weight:500;font-size:11px;color:var(--navy-deep)}
.intro{position:absolute;left:24px;width:330px;font-size:5.3px;line-height:7.2px;color:var(--ink);text-align:justify}
.posture{position:absolute;background:var(--peach);border-radius:7px}
.posture-label{position:absolute;background:var(--orange);color:var(--white);font-weight:500;font-size:8.5px;padding:2px 10px 2px 6px;border-radius:0 8px 8px 0;white-space:nowrap}
.posture-name{position:absolute;font-weight:500;font-size:8px;line-height:10px;color:var(--navy-deep)}
.posture-text{position:absolute;font-size:4.8px;line-height:6.6px;color:var(--ink);text-align:justify}
.posture-text b{font-weight:500;font-size:6.4px;color:var(--navy-deep)}
.posture-photo{position:absolute;border-radius:2px;background:linear-gradient(180deg,#d6a99a 0%,#8d3a3d 30%,#5a4f8f 62%,#2a8fc0 100%)}
.posture-photo--side{background:linear-gradient(90deg,#2a8fc0 0%,#8d3a3d 45%,#5a4f8f 75%,#e9c8b8 100%)}
</style>
</head>
<body>

<section class="spread spread--outer">
  <div class="page page--left back-cover">
    <h2 class="about-title">ABOUT THE TEACHER...</h2>
    <p class="about-body">Mira Halden is a current serving Navy Officer, Yoga Therapist (C-YT) and StillPoint Level 2 instructor. Mira’s classes are about using the practices and teaching of Yoga to come to the essence of your true self and learning to tap into the internal wisdom which is always present. Mira is dedicated to making the resilience developing practices of Yoga accessible to all Australian Military personnel and their families.</p>

    <div class="quote" style="top:107px">
      <svg class="quote-mark" viewBox="0 0 20 16"><path d="M2 15V8C2 4 4 2 8 1M11 15V8C11 4 13 2 17 1" fill="none" stroke="#c98461" stroke-width="1.2"/><path d="M2 15H8V9H2M11 15H17V9H11" fill="none" stroke="#c98461" stroke-width="1.2"/></svg>
      <p class="quote-text">“Posture should be steady and comfortable”<br><br>—Sutras of Aravind Rao</p>
    </div>
    <div class="quote" style="top:150px">
      <svg class="quote-mark" viewBox="0 0 20 16"><path d="M2 15V8C2 4 4 2 8 1M11 15V8C11 4 13 2 17 1" fill="none" stroke="#c98461" stroke-width="1.2"/><path d="M2 15H8V9H2M11 15H17V9H11" fill="none" stroke="#c98461" stroke-width="1.2"/></svg>
      <p class="quote-text">“Tension is who you think you are, Relaxation is who you actually are”</p>
    </div>
    <div class="quote" style="top:184px">
      <svg class="quote-mark" viewBox="0 0 20 16"><path d="M2 15V8C2 4 4 2 8 1M11 15V8C11 4 13 2 17 1" fill="none" stroke="#c98461" stroke-width="1.2"/><path d="M2 15H8V9H2M11 15H17V9H11" fill="none" stroke="#c98461" stroke-width="1.2"/></svg>
      <p class="quote-text">“Life isn’t as serious as the mind makes it out to be”<br>—Elin Marsh</p>
    </div>
    <div class="quote" style="top:225px">
      <svg class="quote-mark" viewBox="0 0 20 16"><path d="M2 15V8C2 4 4 2 8 1M11 15V8C11 4 13 2 17 1" fill="none" stroke="#c98461" stroke-width="1.2"/><path d="M2 15H8V9H2M11 15H17V9H11" fill="none" stroke="#c98461" stroke-width="1.2"/></svg>
      <p class="quote-text">“Watch your thoughts, they become words<br>Watch your words, they become actions<br>Watch your actions, they become habits<br>Watch your habits, they become character<br>Watch your character, for it becomes your destiny”<br>—Upanishads</p>
    </div>

    <svg class="teacher-photo" viewBox="0 0 260 223" role="img" aria-label="Teacher lying in relaxation pose on a yoga mat with a bolster under the knees">
      <defs>
        <linearGradient id="restFill" x1="0" y1="0" x2="0" y2="1">
          <stop offset="0" stop-color="#a15a3c"/>
          <stop offset=".45" stop-color="#8f3c3f"/>
          <stop offset=".75" stop-color="#6a4a7a"/>
          <stop offset="1" stop-color="#b4642f"/>
        </linearGradient>
      </defs>
      <path d="M0 223V120C40 80 90 35 118 0C150 35 215 110 260 223Z" fill="#c98461"/>
      <path d="M7 223V124C45 86 92 42 118 8C146 42 207 112 250 223Z" fill="url(#restFill)"/>
    </svg>
    <p class="website">www.calmdrift.com.au</p>
  </div>

  <div class="page page--right front-cover">
    <svg class="front-art" viewBox="0 0 377 533" preserveAspectRatio="none">
      <defs>
        <clipPath id="coverPanel"><path d="M111 0C72 140 48 330 121 533H377V0Z"/></clipPath>
        <linearGradient id="gardenFill" x1="0" y1="0" x2="0" y2="1">
          <stop offset="0" stop-color="#4f7a37"/>
          <stop offset=".45" stop-color="#7b8a55"/>
          <stop offset=".75" stop-color="#4e6a8d"/>
          <stop offset="1" stop-color="#2b2b2e"/>
        </linearGradient>
      </defs>
      <path d="M103 0C64 140 40 330 113 533H121C48 330 72 140 111 0Z" fill="#c98461"/>
      <g clip-path="url(#coverPanel)">
        <rect x="0" y="0" width="377" height="113" fill="#ffffff"/>
        <rect x="0" y="113" width="377" height="331" fill="url(#gardenFill)" role="img" aria-label="Teacher sitting cross-legged in meditation on a blanket in a park"/>
        <rect x="0" y="444" width="377" height="89" fill="#3b4b65"/>
      </g>
    </svg>
    <div class="brand">
      <span class="brand-dot"></span>
      <div class="brand-name">Calm Drift</div>
      <div class="brand-tagline">Be the change you wish to see in the world</div>
    </div>
    <h1 class="cover-title">Yoga for Sleep Workshop and<br>Restorative Yoga Practice</h1>
  </div>
</section>

<section class="spread spread--inner">
  <div class="page page--left inner-left">
    <h2 class="sequence-title">Yoga for Sleep Workshop Restorative Yoga Sleep Sequence</h2>
    <p class="intro" style="top:42px">Use this sequence to relax and unwind at the end of a day or before bed. Settle comfortably into each posture for about 5-7 minutes. Set a timer to let you know when it is time to change position, and you can also listen to any music you find relaxing at the same time. The audio recording from the Yoga for Sleep Workshop can also be used to recreate the practice at home.</p>
    <p class="intro" style="top:80px">In the middle of the night when you can’t sleep, you might like to try getting up and resting in any one of these postures for about 5-10 minutes before heading back to bed.</p>

    <div class="posture" style="left:24px;top:115px;width:329px;height:183px">
      <span class="posture-label" style="left:13px;top:11px">POSTURE 1 –</span>
      <h3 class="posture-name" style="left:13px;top:33px;width:130px">Supported Chest Opening with Knee Support</h3>
      <p class="posture-text" style="left:13px;top:62px;width:125px"><b>PROPS –</b> 2 x bolsters (or towels rolled up lengthways), 1 x cushion for head support (optional)</p>
      <p class="posture-text" style="left:13px;top:88px;width:125px"><b>SET UP NOTES –</b> Position the props in a T-position with one bolster/towel running parallel to the yoga mat and one bolster towel running horizontal to the mat underneath the knees. Position yourself so your buttocks is on the floor and the parallel bolster runs from the lower back up to behind the head.</p>
      <div class="posture-photo" style="left:150px;top:9px;width:90px;height:137px" role="img" aria-label="Lying back over a lengthways bolster with a bolster under the knees"></div>
      <div class="posture-photo" style="left:252px;top:9px;width:64px;height:137px" role="img" aria-label="Sitting on the mat setting up the bolsters in a T-position"></div>
      <p class="posture-text" style="left:13px;top:152px;width:303px"><b>CAUTION –</b> If any lower back pain is experience adjust the parallel bolster height by using a towel. If using a towel, the height of the parallel support prop can be adjusted by either using a thinner towel or loosely rolling the towel. Do not us any parallel support prop if pain continues.</p>
    </div>

    <div class="posture" style="left:24px;top:316px;width:329px;height:195px">
      <div class="posture-photo" style="left:2px;top:34px;width:98px;height:132px" role="img" aria-label="Bound-angle pose with pillows supporting the knees"></div>
      <div class="posture-photo" style="left:104px;top:34px;width:78px;height:125px" role="img" aria-label="Bound-angle pose with yoga blocks supporting the knees"></div>
      <span class="posture-label" style="left:188px;top:10px">POSTURE 2 –</span>
      <h3 class="posture-name" style="left:188px;top:31px;width:130px">Supported Bound-Angle Pose</h3>
      <p class="posture-text" style="left:188px;top:48px;width:127px"><b>PROPS –</b> 1 x bolsters (or towel rolled up lengthways), 2 x yoga blocks/bolsters (or pillows), 1 x cushion for head support (optional)</p>
      <p class="posture-text" style="left:188px;top:83px;width:127px"><b>SET UP NOTES –</b> Similar to Posture 1 without the bolster behind the knees. Instead, the soles of the feet are together with knees wide being supported by either blocks, bolsters or pillows.</p>
      <p class="posture-text" style="left:188px;top:136px;width:127px"><b>CAUTION –</b> If any lower back pain is experience adjust the parallel bolster height by using a towel. If using a towel, the height of the parallel support prop can be adjusted by either using a thinner towel or loosely rolling the towel. Do not us any parallel support prop if pain continues.</p>
    </div>
  </div>

  <div class="page page--right inner-right">
    <div class="posture" style="left:24px;top:24px;width:329px;height:184px">
      <span class="posture-label" style="left:13px;top:8px">POSTURE 3 –</span>
      <h3 class="posture-name" style="left:13px;top:28px;width:140px">Elevated Legs-Up-the-Wall Pose</h3>
      <p class="posture-text" style="left:13px;top:41px;width:125px"><b>PROPS –</b> 1 x bolsters (or towel or blanket densely folded to a width of about 15-30cm), 1 x cushion for head support (optional)</p>
      <p class="posture-text" style="left:13px;top:76px;width:125px"><b>SET UP NOTES –</b> To enter the posture sit at 90 degrees to the wall with the side of your hip about a hand width away from the wall, and the bolster/folded towel or blanket close by. Lie down on the mat on your side then roll onto your back and extend feet up wall. The feet can push into the wall to elevate the hips slightly so the bolster/folded towel or blanket can slide underneath the hips. The prop should be positioned underneath the sacrum (flat bony structure at the base of the spine).</p>
      <div class="posture-photo posture-photo--side" style="left:164px;top:12px;width:78px;height:140px" role="img" aria-label="Legs up the wall with a folded blanket under the hips"></div>
      <div class="posture-photo posture-photo--side" style="left:234px;top:12px;width:84px;height:140px" role="img" aria-label="Legs up the wall with a bolster under the hips"></div>
      <p class="posture-text" style="left:13px;top:160px;width:305px"><b>CAUTION –</b> If any lower back pain is experience adjust the height the hips are elevated by using a towel or blanket that is folded to a lower height.</p>
    </div>

    <div class="posture" style="left:24px;top:222px;width:329px;height:141px">
      <div class="posture-photo" style="left:12px;top:18px;width:68px;height:95px" role="img" aria-label="Child’s pose resting on a bolster"></div>
      <div class="posture-photo posture-photo--side" style="left:78px;top:18px;width:102px;height:85px" role="img" aria-label="Child’s pose resting on stacked pillows"></div>
      <span class="posture-label" style="left:194px;top:8px">POSTURE 4 –</span>
      <h3 class="posture-name" style="left:194px;top:28px;width:130px">Supported Child’s Pose</h3>
      <p class="posture-text" style="left:194px;top:42px;width:122px"><b>PROPS –</b> 1-2 x bolsters (or 3-4 bed pillows)</p>
      <p class="posture-text" style="left:194px;top:57px;width:122px"><b>SET UP NOTES –</b> Position bolster or stacked pillows under torso. Rest the head in one direction and remember to turn to the head to the other side half way through the time you spend in this posture.</p>
      <p class="posture-text" style="left:194px;top:98px;width:122px"><b>CAUTION –</b> If any knee or hip pain is experience, increase the height of the support under the torso by adding more bolsters, folded blankets or pillows.</p>
    </div>

    <div class="posture" style="left:24px;top:378px;width:329px;height:133px">
      <span class="posture-label" style="left:13px;top:8px">POSTURE 5 –</span>
      <h3 class="posture-name" style="left:13px;top:30px;width:130px">Basic Relaxation Posture with Knee Support</h3>
      <p class="posture-text" style="left:13px;top:54px;width:125px"><b>PROPS –</b> 1x bolsters (or 1 x bed pillows or rolled up towel)</p>
      <p class="posture-text" style="left:13px;top:80px;width:125px"><b>SET UP NOTES –</b> Reclining on back, position bolster or pillows under knees.</p>
      <div class="posture-photo" style="left:164px;top:8px;width:76px;height:118px" role="img" aria-label="Lying on back with a bolster under the knees"></div>
      <div class="posture-photo" style="left:246px;top:8px;width:76px;height:118px" role="img" aria-label="Lying on back with a pillow under the knees"></div>
    </div>
  </div>
</section>

</body>
</html>
```